Create a business promotion flyer to leave in customer mailboxes. We are a bulk petroleum supplier, servicing any industry that requires diesel. Base in griffith NSW, servicing griffith area and surrounds.

Business Name - Terra Diesel
Fuel@terradiesel-example.com.au
Owen - 0491 570 362 ohartley@terradiesel-example.com.au
Liam - 0491 570 718 lprosser@terradiesel-example.com.au
Simon - 0491 570 905 skenway@terradiesel-example.com.au
Office 02 5550 1734

Bulk Fuel deliveries.
Oils & lubricants
Local Family owned business

```html
<!DOCTYPE html>
<html lang="en">
<head>
<meta charset="utf-8">
<title>Terra Diesel – Mailbox Flyer</title>
<link rel="stylesheet" href="https://fonts.googleapis.com/css2?family=Anton&family=Poppins:wght@400;600;700&family=Yellowtail&display=swap">
<style>
  :root {
    --red: #e4262b;
    --charcoal: #3a3a3c;
    --ink: #2c2c2e;
    --white: #ffffff;
    --page: #f1f1f1;
    --gold: #d9a21b;
    --sky: #4b86c9;
    --rule: #cfcfcf;
  }
  * { box-sizing: border-box; margin: 0; padding: 0; }
  html, body { width: 1200px; height: 735px; overflow: hidden; }
  body { background: var(--page); font-family: "Poppins", sans-serif; color: var(--ink); }

  .flyer-frame { position: absolute; left: 355px; top: 20px; width: 491px; height: 695px; box-shadow: 0 4px 14px rgba(0,0,0,.15); }
  .flyer { position: absolute; left: 0; top: 0; width: 964px; height: 1365px; background: var(--white); overflow: hidden; transform: scale(0.5092); transform-origin: 0 0; }

  .flyer-shapes { position: absolute; inset: 0; }

  .brand { position: absolute; left: 40px; top: 120px; display: flex; align-items: center; gap: 18px; }
  .brand-mark { width: 34px; height: 34px; background: var(--red); }
  .brand-name { font-weight: 600; font-size: 74px; color: var(--white); letter-spacing: -1px; line-height: 1; }

  .hero { position: absolute; left: 0; top: 618px; width: 964px; text-align: center; color: var(--white); }
  .hero-title { font-family: "Anton", sans-serif; font-size: 78px; line-height: 1; letter-spacing: 1px; }
  .hero-sub { font-family: "Anton", sans-serif; font-size: 38px; line-height: 1; margin-top: 12px; letter-spacing: 1px; }
  .hero-intro { font-size: 19px; line-height: 1.2; margin: 38px auto 0; width: 830px; }

  .services { position: absolute; left: 0; top: 902px; width: 964px; height: 270px; }
  .service { position: absolute; top: 0; }
  .service-icon { width: 98px; height: 98px; border-radius: 50%; background: var(--red); display: flex; align-items: center; justify-content: center; }
  .service-title { margin-top: 28px; font-weight: 700; font-size: 28px; line-height: 1; text-transform: uppercase; color: var(--ink); }
  .service-text { margin-top: 6px; font-size: 20px; line-height: 1.18; color: var(--ink); }
  .service-divider { position: absolute; top: 120px; width: 2px; height: 145px; background: var(--rule); }

  .contacts { position: absolute; left: 0; top: 1202px; width: 580px; height: 78px; background: var(--charcoal); border-radius: 0 8px 8px 0; display: flex; align-items: center; padding-left: 36px; gap: 20px; }
  .contact { display: flex; align-items: center; gap: 8px; color: var(--white); white-space: nowrap; }
  .contact-name { font-weight: 700; font-size: 18px; line-height: 1; text-transform: uppercase; }
  .contact-phone { font-size: 20px; line-height: 1.05; }

  .local-badge { position: absolute; left: 608px; top: 1190px; white-space: nowrap; }
  .local-script { font-family: "Yellowtail", cursive; color: var(--red); font-size: 46px; line-height: 1; }
  .local-line { font-weight: 700; font-size: 23px; line-height: .95; color: var(--ink); text-transform: uppercase; }

  .footer { position: absolute; left: 38px; top: 1306px; display: flex; align-items: center; gap: 26px; font-size: 17px; line-height: 1.2; color: var(--ink); white-space: nowrap; }
  .footer-item { display: flex; align-items: center; gap: 10px; }
</style>
</head>
<body>
<div class="flyer-frame">
  <article class="flyer">
    <svg class="flyer-shapes" width="964" height="1365" viewBox="0 0 964 1365">
      <defs>
        <linearGradient id="oil" x1="0" y1="0" x2="1" y2="0">
          <stop offset="0" stop-color="#3a3a3c"/>
          <stop offset=".7" stop-color="#6b4412"/>
          <stop offset="1" stop-color="#2a1c0c"/>
        </linearGradient>
        <linearGradient id="yard" x1="0" y1="0" x2="0" y2="1">
          <stop offset="0" stop-color="#4b86c9"/>
          <stop offset=".45" stop-color="#c9d6e4"/>
          <stop offset=".7" stop-color="#b9bcc0"/>
          <stop offset="1" stop-color="#8e9094"/>
        </linearGradient>
        <linearGradient id="splashL" x1="0" y1="0" x2="1" y2="0">
          <stop offset="0" stop-color="#e9b72a" stop-opacity=".9"/>
          <stop offset="1" stop-color="#e9b72a" stop-opacity="0"/>
        </linearGradient>
        <linearGradient id="splashR" x1="1" y1="0" x2="0" y2="0">
          <stop offset="0" stop-color="#e9b72a" stop-opacity=".9"/>
          <stop offset="1" stop-color="#e9b72a" stop-opacity="0"/>
        </linearGradient>
      </defs>
      <rect x="0" y="0" width="964" height="300" fill="var(--charcoal)"/>
      <rect x="560" y="0" width="404" height="190" fill="url(#oil)" role="img" aria-label="Close-up photo of golden oil splashing into dark fuel"/>
      <polygon points="0,262 964,124 964,618 0,588" fill="var(--white)"/>
      <polygon points="0,272 964,142 964,612 0,584" fill="url(#yard)" role="img" aria-label="Photo of a white road-train fuel tanker parked in front of a depot shed under blue sky"/>
      <polygon points="0,587 964,617 964,848 0,875" fill="var(--red)"/>
      <polygon points="520,861 964,836 964,850 520,874" fill="var(--charcoal)"/>
      <rect x="0" y="640" width="110" height="230" fill="url(#splashL)" role="img" aria-label="Golden oil splash decoration"/>
      <rect x="854" y="640" width="110" height="200" fill="url(#splashR)" role="img" aria-label="Golden oil splash decoration"/>
      <rect x="0" y="1352" width="245" height="13" fill="var(--red)"/>
      <rect x="245" y="1352" width="475" height="13" fill="var(--charcoal)"/>
      <rect x="720" y="1352" width="244" height="13" fill="var(--red)"/>
      <rect x="840" y="1182" width="96" height="100" rx="6" fill="var(--red)" role="img" aria-label="Map outline of the Griffith NSW region with location pin"/>
    </svg>

    <div class="brand">
      <span class="brand-mark"></span>
      <span class="brand-name">Terra Diesel</span>
    </div>

    <section class="hero">
      <h1 class="hero-title">FUELING LOCAL INDUSTRY</h1>
      <p class="hero-sub">IN GRIFFITH &amp; SURROUNDS</p>
      <p class="hero-intro">Terra Diesel is a local, family owned business proudly supplying high quality fuel and lubricants to businesses, farms and industry across the Griffith region.</p>
    </section>

    <section class="services">
      <div class="service" style="left:40px">
        <div class="service-icon">
          <svg width="60" height="40" viewBox="0 0 60 40"><rect x="2" y="6" width="34" height="20" rx="10" fill="#fff"/><path d="M38 12h10l8 10v8H38z" fill="#fff"/><rect x="2" y="26" width="54" height="4" fill="#fff"/><circle cx="12" cy="33" r="5" fill="#fff" stroke="#e4262b" stroke-width="2"/><circle cx="24" cy="33" r="5" fill="#fff" stroke="#e4262b" stroke-width="2"/><circle cx="46" cy="33" r="5" fill="#fff" stroke="#e4262b" stroke-width="2"/></svg>
        </div>
        <h2 class="service-title">Bulk Fuel<br>Deliveries</h2>
        <p class="service-text">Reliable on-time delivery<br>of premium diesel to keep<br>your business moving.</p>
      </div>
      <div class="service-divider" style="left:338px"></div>
      <div class="service" style="left:397px">
        <div class="service-icon">
          <svg width="56" height="50" viewBox="0 0 56 50"><path d="M14 8c6 10 10 16 10 22a10 10 0 0 1-20 0c0-6 4-12 10-22z" fill="#fff"/><rect x="28" y="4" width="24" height="42" rx="4" fill="#fff"/><rect x="28" y="16" width="24" height="3" fill="#e4262b"/><rect x="28" y="31" width="24" height="3" fill="#e4262b"/></svg>
        </div>
        <h2 class="service-title">Oils &amp;<br>Lubricants</h2>
        <p class="service-text">High quality products to<br>keep your equipment<br>running at its best.</p>
      </div>
      <div class="service-divider" style="left:676px"></div>
      <div class="service" style="left:728px">
        <div class="service-icon">
          <svg width="40" height="54" viewBox="0 0 40 54"><path d="M10 4h14v6h12v42H4V14z" fill="#fff"/><path d="M20 22c4 7 6 10 6 14a6 6 0 0 1-12 0c0-4 2-7 6-14z" fill="#e4262b"/></svg>
        </div>
        <h2 class="service-title">Petrol<br>Deliveries</h2>
        <p class="service-text">Convenient petrol<br>deliveries for all your<br>business needs.</p>
      </div>
    </section>

    <section class="contacts">
      <div class="contact">
        <svg width="28" height="28" viewBox="0 0 24 24"><path d="M6.6 10.8a15 15 0 0 0 6.6 6.6l2.2-2.2a1 1 0 0 1 1-.25 11.4 11.4 0 0 0 3.6.57 1 1 0 0 1 1 1V20a1 1 0 0 1-1 1A17 17 0 0 1 3 4a1 1 0 0 1 1-1h3.5a1 1 0 0 1 1 1c0 1.250.2 2.450.57 3.570a1 1 0 0 1-.25 1z" fill="#e4262b"/></svg>
        <div><div class="contact-name">Owen</div><div class="contact-phone">0491 570 362</div></div>
      </div>
      <div class="contact">
        <svg width="28" height="28" viewBox="0 0 24 24"><path d="M6.6 10.8a15 15 0 0 0 6.6 6.6l2.2-2.2a1 1 0 0 1 1-.25 11.4 11.4 0 0 0 3.6.57 1 1 0 0 1 1 1V20a1 1 0 0 1-1 1A17 17 0 0 1 3 4a1 1 0 0 1 1-1h3.5a1 1 0 0 1 1 1c0 1.250.2 2.450.57 3.570a1 1 0 0 1-.25 1z" fill="#e4262b"/></svg>
        <div><div class="contact-name">Liam</div><div class="contact-phone">0491 570 718</div></div>
      </div>
      <div class="contact">
        <svg width="28" height="28" viewBox="0 0 24 24"><path d="M6.6 10.8a15 15 0 0 0 6.6 6.6l2.2-2.2a1 1 0 0 1 1-.25 11.4 11.4 0 0 0 3.6.57 1 1 0 0 1 1 1V20a1 1 0 0 1-1 1A17 17 0 0 1 3 4a1 1 0 0 1 1-1h3.5a1 1 0 0 1 1 1c0 1.250.2 2.450.57 3.570a1 1 0 0 1-.25 1z" fill="#e4262b"/></svg>
        <div><div class="contact-name">Simon</div><div class="contact-phone">0491 570 905</div></div>
      </div>
    </section>

    <div class="local-badge">
      <div class="local-script">Local</div>
      <div class="local-line">Family Owned</div>
      <div class="local-line">Business</div>
    </div>

    <footer class="footer">
      <span class="footer-item">
        <svg width="22" height="16" viewBox="0 0 22 16"><rect width="22" height="16" rx="2" fill="#e4262b"/><path d="M1 2l10 7 10-7" stroke="#fff" stroke-width="2" fill="none"/></svg>
        Fuel@terradiesel-example.com.au
      </span>
      <span class="footer-item">
        <svg width="18" height="24" viewBox="0 0 18 24"><path d="M9 0a9 9 0 0 1 9 9c0 6-9 15-9 15S0 15 0 9a9 9 0 0 1 9-9z" fill="#e4262b"/><circle cx="9" cy="9" r="3.5" fill="#fff"/></svg>
        Based in Griffith NSW, servicing Griffith area and surrounds.
      </span>
    </footer>
  </article>
</div>
</body>
</html>
```